Design a Professional Stationery

Hi everyone,
I would like to make a design of stationery for my company Kestrel Wrap (www.kestrelwrap-example.com).
General Info: We are manufacturers of packaging supplies (poly bubble mailers, kraft bubble mailers, bubble wrap, tape, stretch film). We have couple of big warehouses in Los Angeles and New Jersey that serves East and West Coasts. We store lot of boxes with our product. We are wholesalers so we work with big serious distributors.

Project Goals: Create a business stationery that will look professional, modern and straight to the point. Colors: Dark blue, white, light blue (please see the web site). Blue is the color of success.
I want them to be presentable. As you might need to imagine my team will walk around the businesses and leave folders with information at clients table. We will distribute them at the trade shows, business meetings etc.
Updates

Target Market(s)

Business professionals looking for professional wholesaler manufacturer.

Industry/Entity Type

It Company

Font styles to use
Serif
Sans Serif

Colors
3276b5
0255a3
85acd3
cedeed
eaf1f7

Requirements
Must have
• People photos, product photos, add professional warehouse photos, truck, machinery.
Nice to have
• NLP
Should not have
• Use your imagination, no limits so far

```html
<!DOCTYPE html>
<html lang="en">
<head>
<meta charset="utf-8">
<title>Kestrel Wrap — Stationery</title>
<link rel="stylesheet" href="https://fonts.googleapis.com/css2?family=Questrial&display=swap">
<style>
  :root {
    --navy: #0b2b60;
    --navy-deep: #082450;
    --blue: #3276b5;
    --paper: #f2f2f2;
    --ink: #444a55;
    --ink-soft: #6a707a;
    --backdrop: #d3d3d3;
    --sign: #4a5fb0;
  }
  * { margin: 0; padding: 0; box-sizing: border-box; }
  html, body { width: 1200px; height: 1000px; overflow: hidden; }
  body {
    position: relative;
    background: var(--backdrop);
    font-family: "Questrial", "Century Gothic", sans-serif;
    color: var(--ink);
  }
  .piece { position: absolute; overflow: hidden; }

  /* brand lockup: invented name + one plain square */
  .brand {
    position: absolute;
    display: flex;
    align-items: center;
    white-space: nowrap;
    letter-spacing: 0.06em;
    text-transform: uppercase;
  }
  .brand__square { display: inline-block; flex: none; }
  .brand--light { color: #fff; }
  .brand--light .brand__square { background: #fff; }
  .brand--dark { color: var(--navy); }
  .brand--dark .brand__square { background: var(--navy); }

  /* folder */
  .folder {
    left: 152px; top: 41px; width: 431px; height: 559px;
    background: linear-gradient(180deg, #0d3068 0%, var(--navy) 60%, var(--navy-deep) 100%);
    border-radius: 4px;
  }
  .folder__spine {
    position: absolute; top: 0; bottom: 0; width: 1px;
    background: rgba(255,255,255,0.12);
  }
  .folder__spine--a { left: 16px; }
  .folder__spine--b { left: 26px; }
  .folder .brand { left: 173px; top: 100px; font-size: 27px; gap: 10px; }
  .folder .brand__square { width: 18px; height: 18px; }
  .folder__url {
    position: absolute; right: 72px; bottom: 38px;
    color: #fff; font-size: 9.5px; letter-spacing: 0.02em;
  }

  /* letterhead */
  .letterhead {
    left: 616px; top: 61px; width: 417px; height: 539px;
    background: var(--paper);
  }
  .band { position: absolute; left: 0; right: 0; top: 0; height: 6px; background: var(--navy); }
  .letterhead .brand { left: 46px; top: 46px; font-size: 15px; gap: 6px; }
  .letterhead .brand__square { width: 10px; height: 10px; }
  .contact-list { position: absolute; list-style: none; font-size: 6.3px; line-height: 7.4px; color: var(--ink); }
  .contact-list li { display: flex; align-items: center; gap: 3px; }
  .icon { width: 6px; height: 6px; flex: none; }
  .letterhead .contact-list { left: 289px; top: 42px; }
  .letterhead__address { position: absolute; left: 289px; top: 67px; font-size: 6.3px; line-height: 7.4px; }
  .letter {
    position: absolute; left: 38px; top: 175px; width: 341px;
    font-size: 6.2px; line-height: 7.3px; text-align: justify;
  }
  .letter__greeting { font-weight: bold; margin-bottom: 6px; color: #333; }
  .letter p { margin-bottom: 7.3px; }
  .letter__closing { margin-top: 9px; text-align: left; }
  .letter__name { font-weight: bold; color: #333; }
  .signature {
    position: absolute; left: 88px; top: 350px; width: 88px; height: 44px;
    background: linear-gradient(90deg, rgba(74,95,176,0.10), rgba(74,95,176,0.22), rgba(74,95,176,0.10));
    border-radius: 3px;
  }

  /* envelope front */
  .envelope-front {
    left: 117px; top: 630px; width: 466px; height: 202px;
    background: var(--paper);
  }
  .envelope-front .brand { left: 26px; top: 34px; font-size: 15px; gap: 6px; }
  .envelope-front .brand__square { width: 10px; height: 10px; }
  .envelope-front__address {
    position: absolute; left: 26px; top: 175px;
    font-size: 6.3px; line-height: 7.6px;
  }

  /* envelope back */
  .envelope-back {
    left: 616px; top: 630px; width: 466px; height: 202px;
    background: var(--paper);
  }
  .envelope-back__flap { position: absolute; left: 0; top: 0; }
  .envelope-back .brand { left: 200px; top: 29px; font-size: 10px; gap: 4px; }
  .envelope-back .brand__square { width: 7px; height: 7px; }

  /* business cards */
  .card-front {
    left: 410px; top: 860px; width: 180px; height: 100px;
    background: var(--navy);
  }
  .card-front .brand { left: 36px; top: 42px; font-size: 12px; gap: 5px; }
  .card-front .brand__square { width: 8px; height: 8px; }

  .card-back {
    left: 606px; top: 860px; width: 183px; height: 100px;
    background: var(--paper);
  }
  .card-back__band { position: absolute; left: 0; right: 0; top: 50px; height: 40px; background: var(--navy); }
  .card-back__stripe { position: absolute; left: 0; right: 0; top: 90px; height: 10px; background: var(--blue); }
  .card-back__pointer { position: absolute; left: 17px; top: 44px; }
  .card-back__person { position: absolute; left: 19px; top: 25px; }
  .card-back__name { font-size: 6.8px; font-weight: bold; color: var(--blue); letter-spacing: 0.04em; text-transform: uppercase; }
  .card-back__role { font-size: 5.2px; color: var(--ink-soft); margin-top: 1px; }
  .card-back .brand { left: 94px; top: 25px; font-size: 10px; gap: 4px; }
  .card-back .brand__square { width: 7px; height: 7px; }
  .card-back .contact-list { left: 19px; top: 62px; color: #fff; font-size: 4.8px; line-height: 6px; }
  .card-back .contact-list .icon { width: 4.5px; height: 4.5px; }
  .card-back__address {
    position: absolute; right: 10px; top: 64px;
    color: #fff; font-size: 4.8px; line-height: 6px; text-align: right;
  }
</style>
</head>
<body>

  <!-- Presentation folder -->
  <section class="piece folder" aria-label="Presentation folder">
    <span class="folder__spine folder__spine--a"></span>
    <span class="folder__spine folder__spine--b"></span>
    <div class="brand brand--light"><span>Kestrel Wrap</span><span class="brand__square"></span></div>
    <div class="folder__url">www.kestrelwrap-example.com</div>
  </section>

  <!-- Letterhead -->
  <section class="piece letterhead" aria-label="Letterhead">
    <div class="band"></div>
    <div class="brand brand--dark"><span>Kestrel Wrap</span><span class="brand__square"></span></div>
    <ul class="contact-list">
      <li><svg class="icon" viewBox="0 0 6 6"><rect width="6" height="6" fill="#0b2b60"/><path d="M1.6 1.3l.8.0.3.9-.5.4a2.5 2.5 0 0 0 1.2 1.2l.4-.5.9.3v.8c-2 .2-3.3-1.1-3.1-3.1z" fill="#fff"/></svg>555-014-2290</li>
      <li><svg class="icon" viewBox="0 0 6 6"><rect width="6" height="6" fill="#0b2b60"/><rect x="1.1" y="1.8" width="3.8" height="2.5" fill="none" stroke="#fff" stroke-width=".5"/><path d="M1.1 1.8L3 3.2 4.9 1.8" fill="none" stroke="#fff" stroke-width=".5"/></svg>info@kestrelwrap-example.com</li>
      <li><svg class="icon" viewBox="0 0 6 6"><rect width="6" height="6" fill="#0b2b60"/><circle cx="3" cy="3" r="1.7" fill="none" stroke="#fff" stroke-width=".5"/><path d="M1.3 3h3.4M3 1.3v3.4" stroke="#fff" stroke-width=".4"/></svg>www.kestrelwrap-example.com</li>
    </ul>
    <div class="letterhead__address">2400 Harlow Ave<br>Fairmont CA 90000</div>

    <article class="letter">
      <p class="letter__greeting">Dear sir,</p>
      <p>Thank you for your interest in our packaging supplies. We produce poly and kraft bubble mailers, bubble wrap, tape and stretch film for distributors across the country. Our warehouses on both coasts keep large stock ready, so your orders leave quickly and arrive on schedule every time.</p>
      <p>We work as a wholesale manufacturer and partner with serious distributors who need steady supply, fair pricing and clear communication. Every shipment is checked before it leaves our docks. Our team tracks each order from the first call to final delivery, and we share updates at every step so you can plan your own stock with confidence and keep your customers satisfied.</p>
      <p>Enclosed you will find our current catalog and price sheet. Custom sizes, printed mailers and pallet pricing are available on request, and our sales staff will gladly prepare a quote that suits your volume.</p>
      <p>We look forward to working with you. Please reach out with any questions about products, lead times or shipping options, and we will reply within one business day.</p>
      <div class="letter__closing">Yours Sincerely,<br><span class="letter__name">Lena Brooks</span></div>
    </article>
    <div class="signature" role="img" aria-label="Handwritten signature of Lena Brooks"></div>
  </section>

  <!-- Envelope, front -->
  <section class="piece envelope-front" aria-label="Envelope front">
    <div class="band"></div>
    <div class="brand brand--dark"><span>Kestrel Wrap</span><span class="brand__square"></span></div>
    <div class="envelope-front__address">2400 Harlow Ave<br>Fairmont CA 90000</div>
  </section>

  <!-- Envelope, back -->
  <section class="piece envelope-back" aria-label="Envelope back">
    <svg class="envelope-back__flap" width="466" height="66" viewBox="0 0 466 66">
      <polygon points="0,0 466,0 447,65 19,65" fill="#0b2b60"/>
    </svg>
    <div class="brand brand--light"><span>Kestrel Wrap</span><span class="brand__square"></span></div>
  </section>

  <!-- Business card, front -->
  <section class="piece card-front" aria-label="Business card front">
    <div class="brand brand--light"><span>Kestrel Wrap</span><span class="brand__square"></span></div>
  </section>

  <!-- Business card, back -->
  <section class="piece card-back" aria-label="Business card back">
    <div class="card-back__band"></div>
    <div class="card-back__stripe"></div>
    <svg class="card-back__pointer" width="10" height="7" viewBox="0 0 10 7"><polygon points="0,7 5,0 10,7" fill="#0b2b60"/></svg>
    <div class="card-back__person">
      <div class="card-back__name">Jordan Hale</div>
      <div class="card-back__role">General Manager</div>
    </div>
    <div class="brand brand--dark"><span>Kestrel Wrap</span><span class="brand__square"></span></div>
    <ul class="contact-list">
      <li><svg class="icon" viewBox="0 0 6 6"><rect width="6" height="6" fill="#fff"/></svg>555-014-2290</li>
      <li><svg class="icon" viewBox="0 0 6 6"><rect width="6" height="6" fill="#fff"/></svg>info@kestrelwrap-example.com</li>
      <li><svg class="icon" viewBox="0 0 6 6"><rect width="6" height="6" fill="#fff"/></svg>www.kestrelwrap-example.com</li>
    </ul>
    <div class="card-back__address">2400 Harlow Ave<br>Fairmont CA 90000</div>
  </section>

</body>
</html>
```